Marrowby Water Taxi and Transport Business Card

I need business cards for my new water taxi and freight transport business I have started here in Marrowby Alaska. Marrowby is a remote island in the middle of the gulf of Alaska. There are seven native villages around the island and Marrowby is the #2 fishing port in the United States. We also have the largest Coast Guard Base in the U.S. My company will be providing water taxi and freight transport logistics to the villages and many hunting and fishing lodges as well as remote properties around the island.

I would like a business card that isn't status quo, something that stands out, either in feel or appearance. I do like clean minimal designs but it needs to have the necessary contact info on it.

Target Market(s)

remote lodge / property owners, residents of the many villages around Marrowby and any one wanting to enjoy the great outdoors of Marrowby Alaska

Industry/Entity Type

Business

Contact Information for Business Card

I like clean simple designs that aren't cluttered but still provide the necessary information

Colors
0255a3
3277b5
33a4d5
9bcb3c
add136
fbed22
ffc214
f78f20
f37122

Requirements
Must have
• logo and contact info
• Captain Mason Elwick
• www.marrowbyferryline.com
• mason@marrowbyferryline.com

```html
<!DOCTYPE html>
<html lang="en">
<head>
<meta charset="utf-8">
<title>Marrowby Water Taxi and Transport – Business Card</title>
<link rel="stylesheet" href="https://fonts.googleapis.com/css2?family=Open+Sans:wght@400;700&display=swap">
<style>
  :root {
    --navy: #0255a3;
    --mid-blue: #3277b5;
    --sky: #33a4d5;
    --ice: #62d0f2;
    --orange: #f78f20;
    --deep-orange: #f37122;
    --gold: #ffc214;
    --white: #ffffff;
    --stage: #e9ecef;
    --card-w: 520px;
    --card-h: 297px;
  }
  * { box-sizing: border-box; margin: 0; padding: 0; }
  html, body {
    width: 1200px; height: 913px; overflow: hidden;
    background: var(--stage);
    font-family: "Open Sans", Arial, sans-serif;
  }
  .sheet {
    position: relative; width: 1200px; height: 913px;
    display: flex; align-items: center; justify-content: center; gap: 60px;
  }
  .card {
    position: relative; width: var(--card-w); height: var(--card-h);
    border-radius: 16px; overflow: hidden;
    box-shadow: 0 10px 28px rgba(0,0,0,.22);
  }
  .card__art { position: absolute; inset: 0; width: 100%; height: 100%; }

  /* Front */
  .brand {
    position: absolute; left: 34px; top: 58px; color: var(--navy);
  }
  .brand__mark {
    display: inline-block; width: 20px; height: 20px; border-radius: 50%;
    background: var(--orange); vertical-align: middle; margin-right: 8px;
  }
  .brand__name {
    font-weight: 700; font-size: 34px; letter-spacing: 1px; vertical-align: middle;
  }
  .brand__tagline {
    display: block; margin-top: 2px; font-weight: 700; font-size: 14px; padding-left: 2px;
  }
  .holder {
    position: absolute; right: 30px; top: 104px; width: 230px;
    color: var(--white); font-weight: 700; font-size: 18px; text-align: right;
    padding-bottom: 6px; border-bottom: 1px solid rgba(255,255,255,.85);
  }
  .contact {
    position: absolute; left: 30px; bottom: 26px; list-style: none;
    color: var(--white); font-size: 13px; line-height: 20px;
  }
  .contact__item { display: flex; align-items: center; gap: 8px; }
  .contact__icon { width: 12px; height: 12px; flex: none; }

  /* Back */
  .back-brand {
    position: absolute; left: 0; right: 0; top: 96px; text-align: center;
    color: var(--navy); font-weight: 700; font-size: 38px; letter-spacing: 1px;
  }
  .back-brand .brand__mark { width: 24px; height: 24px; margin-right: 10px; }
</style>
</head>
<body>
<main class="sheet">

  <section class="card card--front" aria-label="Business card front">
    <svg class="card__art" viewBox="0 0 520 297" preserveAspectRatio="none" aria-hidden="true">
      <defs>
        <linearGradient id="frontSky" x1="0" y1="0" x2="1" y2="1">
          <stop offset="0" stop-color="#62d0f2"/>
          <stop offset=".55" stop-color="#33a4d5"/>
          <stop offset="1" stop-color="#3277b5"/>
        </linearGradient>
        <linearGradient id="frontDeep" x1="0" y1="0" x2="0" y2="1">
          <stop offset="0" stop-color="#2a73c0"/>
          <stop offset="1" stop-color="#0255a3"/>
        </linearGradient>
      </defs>
      <rect width="520" height="297" fill="url(#frontSky)"/>
      <path d="M0 297 L0 252 C130 246 230 205 300 125 C365 55 430 38 520 34 L520 297 Z" fill="url(#frontDeep)"/>
      <path d="M150 250 C230 232 270 190 310 135 C365 62 430 40 520 34" fill="none" stroke="#f78f20" stroke-width="6"/>
      <line x1="150" y1="252" x2="520" y2="252" stroke="rgba(255,255,255,.35)" stroke-width="1"/>
    </svg>

    <div class="brand">
      <span class="brand__mark"></span><span class="brand__name">MARROWBY</span>
      <span class="brand__tagline">Water Taxi &amp; Transport</span>
    </div>

    <p class="holder">Captain Mason Elwick</p>

    <ul class="contact">
      <li class="contact__item">
        <svg class="contact__icon" viewBox="0 0 12 12" aria-hidden="true"><rect x="1" y="2.5" width="10" height="7" rx="1" fill="none" stroke="#ffc214" stroke-width="1.2"/><path d="M1.5 3 L6 6.5 L10.5 3" fill="none" stroke="#ffc214" stroke-width="1.2"/></svg>
        mason@marrowbyferryline.com
      </li>
      <li class="contact__item">
        <svg class="contact__icon" viewBox="0 0 12 12" aria-hidden="true"><circle cx="6" cy="6" r="5" fill="none" stroke="#ffc214" stroke-width="1.2"/><ellipse cx="6" cy="6" rx="2.2" ry="5" fill="none" stroke="#ffc214" stroke-width="1"/><line x1="1" y1="6" x2="11" y2="6" stroke="#ffc214" stroke-width="1"/></svg>
        www.marrowbyferryline.com
      </li>
    </ul>
  </section>

  <section class="card card--back" aria-label="Business card back">
    <svg class="card__art" viewBox="0 0 520 297" preserveAspectRatio="none" aria-hidden="true">
      <defs>
        <linearGradient id="backBand" x1="0" y1="1" x2="1" y2="0">
          <stop offset="0" stop-color="#f37122"/>
          <stop offset="1" stop-color="#f9a03a"/>
        </linearGradient>
      </defs>
      <rect width="520" height="297" fill="#ffffff"/>
      <path d="M0 297 L0 262 C70 205 200 196 320 156 C420 122 480 88 520 64 L520 297 Z" fill="url(#backBand)"/>
      <path d="M0 252 C70 196 200 186 320 146 C420 112 480 78 520 54" fill="none" stroke="#33a4d5" stroke-width="3"/>
    </svg>

    <div class="back-brand"><span class="brand__mark"></span>MARROWBY</div>
  </section>

</main>
</body>
</html>
```